Corporate Design für die Vela Serena! GmbH
Zielgruppe
Die Vela Serena! GmbH begibt sich auf den Weg mit den Firmen, die sie gründet, kauft, entwickelt und verkauft. Wir sind eine Holding, beteiligen uns an Firmen oder gründen diese neu. 'Vela Serena!' ist der Pilgergruß auf dem Jakobsweg - diesen bin ich schon 5 Mal gegangen und die Metapher 'Gründen als Weg/Pilgerreise' finde ich sehr zutreffend. Ferner gibt es einen gelben Pfeil auf dem Jakobsweg, der einen immer verfolgt und einem den Weg weist. Das sind wir auch.
Aufgabenstellung
Es ist am Ende das Tages eine Holding, bei der sich Gründer und Firmen melden sollen, weil sie Beratung oder Kapital brauchen - daher ist Seriosität zwar unbedingt notwendig aber sie soll nicht abschrecken, elitär, 'Anwalt-grau-blau-weiß-bieder' sein. Gründertum, Unternehmertum, Freude, Machen, Erfolg!
Pilgern macht Freude und Gründen und Firmen haben auch. Mit uns um so mehr! Ein toller Weg!
'Vela Serena!' eben
Wir heißen 'Vela Serena! GmbH' - mit einem Ausrufezeichen angemeldet und das ist wichtig. Wir haben keine 'Fragezeichen' oder 'Punkte' wir haben ein Ausrufezeichen und einen Pfeil, ein Ziel, einen Weg, Etappen...
Die Abkürzung 'VS!' kann eine Möglichkeit sein aber ausgeschrieben wäre mir lieber - VS! kann das Favicon oder eine Logo-Kurzform/Variante sein

```html
<!DOCTYPE html>
<html lang="de">
<head>
<meta charset="utf-8">
<title>Vela Serena! GmbH – Corporate Design</title>
<link rel="stylesheet" href="https://fonts.googleapis.com/css2?family=Montserrat:wght@400;600&display=swap">
<style>
  :root {
    --ink: #333333;
    --yellow: #ffc600;
    --paper: #ffffff;
    --window: #cfcfcf;
    --faint: #eeeeee;
  }
  * { margin: 0; padding: 0; box-sizing: border-box; }
  html, body { width: 1200px; height: 5108px; overflow: hidden; background: var(--paper); }
  body { position: relative; font-family: "Montserrat", sans-serif; color: var(--ink); }
  .abs { position: absolute; }
  svg { display: block; overflow: visible; }

  .name { font-family: "Montserrat", sans-serif; font-weight: 400; white-space: nowrap; line-height: 1; }
  .name-center { position: absolute; left: 0; width: 100%; text-align: center; }
  .mark { position: absolute; border-radius: 50%; border-style: solid; }

  .piece { position: absolute; background: var(--paper); box-shadow: 0 6px 14px rgba(0,0,0,.28); overflow: hidden; }
  .bar-top { position: absolute; left: 0; top: 0; width: 100%; background: var(--yellow); }
  .bar-bottom { position: absolute; left: 0; bottom: 0; width: 100%; background: var(--ink); }

  .sender-line { font-size: 12px; font-weight: 600; white-space: nowrap; }
  .window-mark { position: absolute; width: 12px; height: 12px; border-color: var(--ink); border-style: solid; border-width: 0; }
  .contact { font-size: 15px; line-height: 22px; }
  .contact-row, .card-contact-row { display: flex; align-items: center; gap: 10px; white-space: nowrap; }
  .icon { width: 12px; height: 12px; flex: none; }
  .fold { position: absolute; left: 0; width: 14px; height: 1px; background: var(--ink); }
  .footer-band { position: absolute; left: 0; bottom: 0; width: 100%; height: 92px; background: var(--ink); color: #fff; }
  .footer-rule { position: absolute; left: 0; width: 100%; height: 4px; background: var(--yellow); }
  .footer-col { position: absolute; top: 16px; padding-left: 8px; border-left: 2px solid #fff; font-size: 14px; line-height: 19px; white-space: nowrap; }

  .card-dark { background: var(--ink); }
  .card-half { position: absolute; top: 0; right: 0; height: 100%; background: var(--ink); }
  .person { position: absolute; left: 12px; font-size: 14px; line-height: 16px; }
  .person b { font-weight: 600; display: block; }
  .person span { font-size: 11px; }
  .card-address { position: absolute; left: 12px; font-size: 11px; line-height: 14px; }
  .card-contact { position: absolute; font-size: 11px; line-height: 18px; }
  .card-contact .icon { width: 9px; height: 9px; }
  .on-dark { color: #fff; }

  .window { position: absolute; background: var(--window); border-radius: 24px; }
</style>
</head>
<body>

  <!-- Primary lockup -->
  <section class="abs" style="left:0;top:0;width:1200px;height:640px;">
    <div class="mark" style="left:476px;top:104px;width:256px;height:256px;border-width:10px;border-color:var(--ink)"></div>
    <p class="name name-center" style="top:420px;font-size:116px;color:var(--ink)">Vela Serena!</p>
  </section>

  <!-- Secondary lockup -->
  <section class="abs" style="left:0;top:900px;width:1200px;height:460px;">
    <div class="mark" style="left:476px;top:20px;width:256px;height:256px;border-width:10px;border-color:var(--ink)"></div>
    <p class="name name-center" style="top:336px;font-size:116px;color:var(--ink)">Vela Serena!</p>
  </section>

  <!-- Letterhead -->
  <article class="piece letterhead" style="left:84px;top:1624px;width:1018px;height:1436px;">
    <div class="bar-top" style="height:12px"></div>

    <div class="mark" style="left:768px;top:64px;width:72px;height:72px;border-width:4px;border-color:var(--ink)"></div>
    <p class="abs name" style="right:44px;top:150px;font-size:38px;color:var(--ink)">Vela Serena!</p>

    <div class="window-mark" style="left:108px;top:212px;border-left-width:1px;border-top-width:1px"></div>
    <div class="window-mark" style="left:510px;top:212px;border-right-width:1px;border-top-width:1px"></div>
    <div class="window-mark" style="left:108px;top:420px;border-left-width:1px;border-bottom-width:1px"></div>
    <div class="window-mark" style="left:510px;top:420px;border-right-width:1px;border-bottom-width:1px"></div>
    <p class="abs sender-line" style="left:120px;top:224px">Vela Serena! GmbH | Musterstrasse 123 | 12345 Musterstadt</p>

    <div class="abs contact" style="left:772px;top:220px">
      <div class="contact-row"><svg class="icon" viewBox="0 0 12 12"><path d="M2 1h3l1 3-2 1a7 7 0 0 0 3 3l1-2 3 1v3c-6 0-9-3-9-9z" fill="var(--ink)"/></svg>+41 123 / 45 67 89 01</div>
      <div class="contact-row"><svg class="icon" viewBox="0 0 12 12"><rect x="3" y="1" width="6" height="4" fill="var(--ink)"/><rect x="1" y="6" width="10" height="5" fill="var(--ink)"/></svg>+41 123 / 45 67 89 01</div>
      <div class="contact-row"><svg class="icon" viewBox="0 0 12 12"><rect x="1" y="2.5" width="10" height="7" fill="var(--ink)"/><path d="M1 3l5 4 5-4" stroke="#fff" fill="none"/></svg>info@vela-serena.de</div>
      <div class="contact-row"><svg class="icon" viewBox="0 0 12 12"><circle cx="6" cy="6" r="5" fill="none" stroke="var(--ink)" stroke-width="1.4"/><path d="M1 6h10M6 1c-3 3-3 7 0 10M6 1c3 3 3 7 0 10" stroke="var(--ink)" fill="none"/></svg>www.vela-serena.de</div>
    </div>

    <div class="fold" style="top:502px"></div>
    <div class="fold" style="top:1012px"></div>

    <div class="mark" aria-hidden="true" style="left:334px;top:928px;width:372px;height:372px;border-width:10px;border-color:var(--faint)"></div>

    <div class="footer-rule" style="top:1336px"></div>
    <footer class="footer-band">
      <div class="footer-col" style="left:96px">Musterstrasse 123<br>12345 Musterstadt<br>Geschäftsführung Max Muster</div>
      <div class="footer-col" style="left:382px">Bankverbindung<br>BIC:&nbsp; ABCDEFGHXXX<br>IBAN: DE 00 0000 0000 0000 0000 00</div>
      <div class="footer-col" style="left:764px">Finanzamt<br>Musterstadt<br>USt-IdNr.: DE000000000</div>
    </footer>
  </article>

  <!-- Business card, dark front -->
  <article class="piece card-dark" style="left:98px;top:3146px;width:482px;height:312px;">
    <div class="mark" style="left:197px;top:84px;width:88px;height:88px;border-width:5px;border-color:#fff"></div>
    <p class="name name-center" style="top:196px;font-size:44px;color:#fff">Vela Serena!</p>
  </article>

  <!-- Business card, split back -->
  <article class="piece" style="left:630px;top:3146px;width:482px;height:312px;">
    <div class="card-half" style="width:240px">
      <div class="mark" style="left:96px;top:28px;width:48px;height:48px;border-width:3px;border-color:#fff"></div>
      <p class="name name-center" style="top:90px;font-size:27px;color:#fff">Vela Serena!</p>
    </div>
    <div class="person" style="top:170px"><b>MAX MUSTER</b><span>Patentanwalt</span></div>
    <div class="card-address" style="top:272px">Musterstrasse 123<br>12345 Musterstadt</div>
    <div class="card-contact on-dark" style="left:256px;top:208px">
      <div class="card-contact-row"><svg class="icon" viewBox="0 0 12 12"><path d="M2 1h3l1 3-2 1a7 7 0 0 0 3 3l1-2 3 1v3c-6 0-9-3-9-9z" fill="#fff"/></svg>+41 123 / 45 67 89 01</div>
      <div class="card-contact-row"><svg class="icon" viewBox="0 0 12 12"><rect x="3" y="1" width="6" height="4" fill="#fff"/><rect x="1" y="6" width="10" height="5" fill="#fff"/></svg>+41 123 / 45 67 89 01</div>
      <div class="card-contact-row"><svg class="icon" viewBox="0 0 12 12"><rect x="3" y="0" width="6" height="12" rx="1" fill="#fff"/></svg>+41 123 / 45 67 89 01</div>
      <div class="card-contact-row"><svg class="icon" viewBox="0 0 12 12"><rect x="1" y="2.5" width="10" height="7" fill="#fff"/></svg>info@vela-serena.de</div>
      <div class="card-contact-row"><svg class="icon" viewBox="0 0 12 12"><circle cx="6" cy="6" r="5" fill="none" stroke="#fff" stroke-width="1.4"/><path d="M1 6h10" stroke="#fff"/></svg>www.vela-serena.de</div>
    </div>
  </article>

  <!-- Business card, white front -->
  <article class="piece" style="left:98px;top:3534px;width:482px;height:310px;">
    <div class="bar-top" style="height:12px"></div>
    <div class="bar-bottom" style="height:10px"></div>
    <div class="mark" style="left:197px;top:84px;width:88px;height:88px;border-width:5px;border-color:var(--ink)"></div>
    <p class="name name-center" style="top:196px;font-size:44px;color:var(--ink)">Vela Serena!</p>
  </article>

  <!-- Business card, white back -->
  <article class="piece" style="left:630px;top:3534px;width:482px;height:310px;">
    <div class="bar-top" style="height:12px"></div>
    <div class="bar-bottom" style="height:10px"></div>
    <div class="mark" style="left:330px;top:42px;width:48px;height:48px;border-width:3px;border-color:var(--ink)"></div>
    <p class="abs name" style="right:16px;top:100px;font-size:27px;color:var(--ink)">Vela Serena!</p>
    <div class="person" style="top:170px"><b>MAX MUSTER</b><span>Patentanwalt</span></div>
    <div class="card-address" style="top:264px">Musterstrasse 123<br>12345 Musterstadt</div>
    <div class="card-contact" style="left:302px;top:190px">
      <div class="card-contact-row"><svg class="icon" viewBox="0 0 12 12"><path d="M2 1h3l1 3-2 1a7 7 0 0 0 3 3l1-2 3 1v3c-6 0-9-3-9-9z" fill="var(--ink)"/></svg>+41 123 / 45 67 89 01</div>
      <div class="card-contact-row"><svg class="icon" viewBox="0 0 12 12"><rect x="3" y="1" width="6" height="4" fill="var(--ink)"/><rect x="1" y="6" width="10" height="5" fill="var(--ink)"/></svg>+41 123 / 45 67 89 01</div>
      <div class="card-contact-row"><svg class="icon" viewBox="0 0 12 12"><rect x="3" y="0" width="6" height="12" rx="1" fill="var(--ink)"/></svg>+41 123 / 45 67 89 01</div>
      <div class="card-contact-row"><svg class="icon" viewBox="0 0 12 12"><rect x="1" y="2.5" width="10" height="7" fill="var(--ink)"/></svg>info@vela-serena.de</div>
      <div class="card-contact-row"><svg class="icon" viewBox="0 0 12 12"><circle cx="6" cy="6" r="5" fill="none" stroke="var(--ink)" stroke-width="1.4"/><path d="M1 6h10" stroke="var(--ink)"/></svg>www.vela-serena.de</div>
    </div>
  </article>

  <!-- Envelope, front -->
  <article class="piece" style="left:90px;top:3964px;width:1028px;height:508px;">
    <div class="bar-top" style="height:12px"></div>
    <div class="bar-bottom" style="height:14px"></div>
    <div class="mark" style="left:262px;top:128px;width:56px;height:56px;border-width:4px;border-color:var(--ink)"></div>
    <p class="abs name" style="left:90px;width:402px;text-align:center;top:194px;font-size:30px;color:var(--ink)">Vela Serena!</p>
    <div class="window" style="left:90px;top:242px;width:402px;height:200px"></div>
  </article>

  <!-- Envelope, back -->
  <article class="piece" style="left:90px;top:4546px;width:1028px;height:514px;">
    <svg class="abs" style="left:0;top:0" width="1028" height="148" viewBox="0 0 1028 148">
      <path d="M0 0H1028L982 124Q974 144 950 144H78Q54 144 46 124Z" fill="var(--yellow)"/>
    </svg>
    <div class="bar-bottom" style="height:14px"></div>
    <div class="mark" style="left:478px;top:16px;width:72px;height:72px;border-width:4px;border-color:#fff"></div>
    <p class="name name-center" style="top:100px;font-size:36px;color:#fff">Vela Serena!</p>
  </article>

</body>
</html>
```